TALMORK

The business want a professional looking business card. We have a scetch we will add but want the extra upgrade, and would like more suggestions for variations of our business cards.

```html
<!DOCTYPE html>
<html lang="en">
<head>
<meta charset="utf-8">
<title>TALMORK Business Card</title>
<link rel="stylesheet" href="https://fonts.googleapis.com/css2?family=Playfair+Display:wght@700;800&family=Montserrat:wght@400;500;600&display=swap">
<style>
  :root {
    --page-bg: #3a3a3a;
    --card-black: #141414;
    --card-edge: #1c1c1c;
    --gold: #d4a62c;
    --gold-light: #f0cf62;
    --silver: #c9c9c9;
    --text-white: #f2f2f2;
  }
  * { box-sizing: border-box; margin: 0; padding: 0; }
  html, body {
    width: 1200px; height: 875px; overflow: hidden;
    background: var(--page-bg);
  }
  .canvas {
    position: relative; width: 1200px; height: 875px;
    display: flex; align-items: center; justify-content: center; gap: 40px;
  }
  .card {
    position: relative; width: 540px; height: 310px;
    background: var(--card-black);
    border-radius: 16px;
    border: 1.5px solid var(--gold);
    overflow: hidden;
  }
  /* Back side */
  .card--back {
    background: linear-gradient(135deg, #2a2a2a 0%, #1a1a1a 40%, var(--card-black) 100%);
    display: flex; align-items: center; justify-content: center; gap: 16px;
  }
  .brand-mark--back {
    display: flex; align-items: center; gap: 14px;
  }
  .brand-mark--back .brand-dot {
    width: 34px; height: 34px; border-radius: 50%; background: var(--silver);
  }
  .brand-mark--back .brand-name {
    font-family: "Playfair Display", serif; font-weight: 700;
    font-size: 40px; letter-spacing: 4px; color: var(--silver);
  }
  /* Front side */
  .card--front { padding: 34px 36px; }
  .wordmark {
    font-family: "Playfair Display", serif; font-weight: 700;
    font-size: 34px; letter-spacing: 5px; color: var(--gold);
    line-height: 1;
  }
  .person-name {
    margin-top: 40px;
    font-family: "Playfair Display", serif; font-weight: 800;
    font-size: 23px; color: var(--gold); line-height: 1.1;
  }
  .person-title {
    margin-top: 6px;
    font-family: "Montserrat", sans-serif; font-weight: 500;
    font-size: 13px; color: var(--text-white);
  }
  .contact-list {
    list-style: none; margin-top: 24px;
    font-family: "Montserrat", sans-serif; font-size: 12.5px; color: var(--text-white);
  }
  .contact-list li { display: flex; align-items: center; gap: 9px; margin-bottom: 6px; }
  .contact-icon { width: 12px; height: 12px; flex: none; }
  .brand-mark--front {
    position: absolute; right: 44px; top: 60px;
    display: flex; flex-direction: column; align-items: center; gap: 14px;
  }
  .brand-mark--front .brand-dot {
    width: 120px; height: 120px; border-radius: 50%; background: var(--gold);
  }
  .brand-mark--front .brand-name {
    font-family: "Playfair Display", serif; font-weight: 700;
    font-size: 18px; letter-spacing: 3px; color: var(--gold);
  }
</style>
</head>
<body>
<main class="canvas">
  <section class="card card--back" aria-label="Card back">
    <div class="brand-mark brand-mark--back">
      <span class="brand-dot"></span>
      <span class="brand-name">TALMORK</span>
    </div>
  </section>

  <section class="card card--front" aria-label="Card front">
    <div class="wordmark">TALMORK</div>
    <div class="person-name">Aksel Brenna Halvorsen</div>
    <div class="person-title">CEO &amp; Founder</div>
    <ul class="contact-list">
      <li>
        <svg class="contact-icon" viewBox="0 0 24 24"><path fill="#d4a62c" d="M6.6 10.8a15.1 15.1 0 0 0 6.6 6.6l2.2-2.2a1 1 0 0 1 1-.25 11.4 11.4 0 0 0 3.6.57 1 1 0 0 1 1 1V20a1 1 0 0 1-1 1A17 17 0 0 1 3 4a1 1 0 0 1 1-1h3.5a1 1 0 0 1 1 1c0 1.25.2 2.45.57 3.57a1 1 0 0 1-.25 1z"/></svg>
        004791234567
      </li>
      <li>
        <svg class="contact-icon" viewBox="0 0 24 24"><path fill="#d4a62c" d="M2 5h20v14H2z"/><path fill="none" stroke="#141414" stroke-width="2" d="M2 5l10 8 10-8"/></svg>
        talmork.co@mailbox.com
      </li>
      <li>
        <svg class="contact-icon" viewBox="0 0 24 24"><circle cx="12" cy="12" r="10" fill="none" stroke="#d4a62c" stroke-width="2"/><path fill="none" stroke="#d4a62c" stroke-width="1.6" d="M2 12h20M12 2c3 3 3 17 0 20M12 2c-3 3-3 17 0 20"/></svg>
        www.talmork.co
      </li>
    </ul>
    <div class="brand-mark brand-mark--front">
      <span class="brand-dot"></span>
      <span class="brand-name">TALMORK</span>
    </div>
  </section>
</main>
</body>
</html>
```